Global (re)insurance broker needs a business card design

We need a classic business card for our company that is headquartered in SG, with offices in Malaysia and Dubai. We specialise in insurance and reinsurance broking and consultancy for our global clients.

```html
<!DOCTYPE html>
<html lang="en">
<head>
<meta charset="utf-8">
<title>Koraven Business Card</title>
<link rel="stylesheet" href="https://fonts.googleapis.com/css2?family=Arimo:wght@400;700&display=swap">
<style>
  :root {
    --backdrop: #e4e4e2;
    --card: #333333;
    --card-edge: #2447a8;
    --brand-blue: #2a4aa3;
    --brand-green: #c8e3c2;
    --ink-light: #f2f2f2;
    --rule: #9a9a9a;
  }
  * { box-sizing: border-box; margin: 0; padding: 0; }
  html, body {
    width: 1200px; height: 802px; overflow: hidden;
    background: var(--backdrop);
    font-family: "Arimo", Arial, sans-serif;
  }
  .stage {
    width: 1200px; height: 802px;
    display: flex; align-items: center; justify-content: center; gap: 56px;
  }
  .card {
    position: relative;
    width: 525px; height: 300px;
    background: var(--card);
    border-bottom: 3px solid var(--card-edge);
    border-left: 2px solid var(--card-edge);
    box-shadow: 0 10px 24px rgba(0,0,0,0.25);
    color: var(--ink-light);
  }
  .wordmark {
    font-weight: 700;
    letter-spacing: 1px;
    color: var(--brand-green);
  }
  .card-front .wordmark {
    position: absolute; left: 0; right: 0; top: 52px;
    text-align: center;
    font-size: 52px;
  }
  .holder {
    position: absolute; left: 92px; top: 148px;
    width: 170px; text-align: right;
    padding-right: 16px;
    border-right: 1px solid var(--rule);
    height: 58px;
  }
  .holder-name {
    font-size: 18px; font-weight: 700; color: var(--brand-blue);
    text-transform: uppercase; letter-spacing: 0.5px;
  }
  .holder-role { font-size: 15px; margin-top: 4px; }
  .contacts {
    position: absolute; left: 278px; top: 140px;
    list-style: none; font-size: 14px; line-height: 24px;
  }
  .contacts li { display: flex; align-items: center; gap: 8px; }
  .contacts svg { width: 12px; height: 12px; flex: none; }
  .address {
    position: absolute; left: 0; right: 0; top: 238px;
    text-align: center; font-size: 14px;
  }
  .card-back { display: flex; align-items: center; justify-content: center; }
  .card-back .wordmark { font-size: 64px; }
</style>
</head>
<body>
<main class="stage">
  <section class="card card-front">
    <div class="wordmark">KORAVEN</div>
    <div class="holder">
      <div class="holder-name">Daniel Reyes</div>
      <div class="holder-role">Manager</div>
    </div>
    <ul class="contacts">
      <li>
        <svg viewBox="0 0 12 12"><path d="M2.5 1h2l1 2.5-1.3 1a6 6 0 0 0 3.3 3.3l1-1.3 2.5 1v2a1 1 0 0 1-1 1A9.5 9.5 0 0 1 1.5 2a1 1 0 0 1 1-1z" fill="var(--ink-light)"/></svg>
        555-318-7402
      </li>
      <li>
        <svg viewBox="0 0 12 12"><rect x="1" y="2.5" width="10" height="7" fill="none" stroke="var(--ink-light)" stroke-width="1.2"/><path d="M1 2.5l5 4 5-4" fill="none" stroke="var(--ink-light)" stroke-width="1.2"/></svg>
        hello@koraven.net
      </li>
      <li>
        <svg viewBox="0 0 12 12"><circle cx="6" cy="6" r="5" fill="none" stroke="var(--ink-light)" stroke-width="1.1"/><ellipse cx="6" cy="6" rx="2.2" ry="5" fill="none" stroke="var(--ink-light)" stroke-width="1"/><path d="M1 6h10" stroke="var(--ink-light)" stroke-width="1"/></svg>
        www.koraven.net
      </li>
    </ul>
    <p class="address">Your Address, City, State, Zip 0000</p>
  </section>

  <section class="card card-back">
    <div class="wordmark">KORAVEN</div>
  </section>
</main>
</body>
</html>
```